How likely are people to engage in social distancing? We need a good illustration to show the data!

We surveyed U.S. adults March 20th - 24th, 2020 and asked how likely they were to engage in social distancing (and other COVID-19 related health behaviors). What did the survey find? Basically, most people intend to engage in social distancing behaviors (e.g., avoiding large crowds) and other behaviors that reduce the spread of COVID-19 (e.g., washing hands at least 20 seconds). When most people intend to engage in a behavior, then public health professionals try to leverage that to move more people to act.
Now we need innovative and professional images that attempt to communicate one or all of these findings. The specific findings are nicely summarized in the attached document. For example, 82% of participants intend to engage in social distancing.
What sort of visual are we looking for? Our preference is for an original illustration (or set of illustrations). Our preference is for (creative and powerful illustrations, but we are also open to the creative and well-executed infographics.
We need these images fast . We will award monetary prizes to the 3 best designs. If we like more than that, then we might purchase more (e.g., in past contests, we have purchased as many as 30 designs).
What we will need:
(1) The illustrations must be original and we will need the photoshop and/or illustrator files for all artwork.
(2) You can illustrate all of the findings or just one of them. We need creative approaches that do a lucid job of bringing the data to life. Most people intend to engage in these behaviors. How to communicate that? Republicans and Democrats do not differ in their intentions; how to communicate that?
(3) The illustration should say, somewhere: "Based on a survey of 400 U.S. adults conducted March 20 - 24th, 2020."

U.S. Adults

• Original illustrations based on the findings of the survey (see attached document).

```html
<!DOCTYPE html>
<html lang="en">
<head>
<meta charset="utf-8">
<title>Behaviors to Slow the Spread of Coronavirus</title>
<link rel="stylesheet" href="https://fonts.googleapis.com/css2?family=Fira+Sans+Condensed:wght@500;600;700;800&family=Open+Sans:ital,wght@1,700&family=Dancing+Script:wght@600&display=swap">
<style>
  :root {
    --navy: #27307a;
    --navy-deep: #13294b;
    --ink: #3b3b3f;
    --label: #1d1d1f;
    --blue: #3469b8;
    --blue-text: #2d5aa8;
    --red: #ec2a22;
    --red-text: #e53124;
    --panel: #e6e7e9;
    --panel-light: #f6f7f8;
    --white: #ffffff;
  }
  * { margin: 0; padding: 0; box-sizing: border-box; }
  html, body { width: 978px; height: 1200px; overflow: hidden; background: var(--white); }
  .canvas { position: relative; width: 978px; height: 1200px; overflow: hidden; background: var(--white); font-family: "Fira Sans Condensed", sans-serif; }

  .survey-band { position: absolute; left: 65px; top: 2px; width: 848px; height: 58px; background: var(--navy);
    color: var(--white); font-family: "Open Sans", sans-serif; font-style: italic; font-weight: 700; font-size: 21.5px;
    display: flex; align-items: center; justify-content: center; letter-spacing: 0.1px; }

  .header { position: absolute; left: 65px; top: 60px; width: 848px; height: 290px; }
  .header-art { position: absolute; inset: 0;
    background: radial-gradient(circle at 88% 40%, #d6dbe6 0, rgba(214,219,230,0.6) 90px, rgba(255,255,255,0) 170px),
                radial-gradient(circle at 5% 10%, #e1e5ee 0, rgba(255,255,255,0) 90px),
                radial-gradient(circle at 60% 55%, #e8ebf1 0, rgba(255,255,255,0) 60px),
                var(--white); }
  .title { position: absolute; left: 70px; top: 20px; }
  .title-lead { font-size: 36px; font-weight: 700; color: var(--ink); line-height: 1; white-space: nowrap; }
  .title-blue { font-size: 52px; font-weight: 800; color: var(--blue); line-height: 1; margin-top: 14px; letter-spacing: -0.5px; text-shadow: 2px 2px 2px rgba(0,0,0,0.25); }
  .title-red { font-size: 64px; font-weight: 800; color: var(--red); line-height: 1; letter-spacing: -0.5px; text-shadow: 2px 2px 2px rgba(0,0,0,0.25); }
  .title-row { display: flex; align-items: baseline; margin-top: 8px; }
  .title-script { font-family: "Dancing Script", cursive; font-size: 34px; color: #111; margin: 0 22px 0 10px; }
  .title-red.second { margin-top: 6px; }

  .chart-panel { position: absolute; left: 65px; top: 350px; width: 848px; height: 744px;
    background: radial-gradient(ellipse at 50% 45%, var(--panel-light) 0, #eceef0 45%, #cfd1d4 100%); }
  .map-area { position: absolute; left: 46px; top: 43px; width: 700px; height: 380px; opacity: 0.55;
    background: radial-gradient(ellipse at 45% 45%, #c7c8ca 0, rgba(199,200,202,0.5) 55%, rgba(199,200,202,0) 72%);
    border-radius: 40% 30% 45% 35%; }

  .legend { position: absolute; top: 52px; left: 238px; display: flex; align-items: center; font-weight: 700; font-size: 25px; color: #2b2b2b; letter-spacing: 0.3px; }
  .swatch { width: 42px; height: 26px; margin-right: 18px; }
  .swatch.dem { background: var(--blue); }
  .swatch.rep { background: var(--red); margin-left: 30px; }

  .rows { position: absolute; left: 0; top: 0; }
  .row { position: absolute; left: 0; width: 848px; height: 50px; }
  .row-label { position: absolute; left: 72px; width: 290px; top: 50%; transform: translateY(-50%); font-weight: 600; font-size: 16px; line-height: 1.25; color: var(--label); letter-spacing: 0.2px; }
  .bar { position: absolute; left: 363px; height: 14px; box-shadow: 2px 2px 0 #2c2c2c; }
  .bar.dem { top: 0; background: var(--blue); }
  .bar.rep { top: 19px; background: var(--red); }
  .pct { position: absolute; font-weight: 800; font-size: 20px; line-height: 1; text-shadow: 1px 1px 0 #fff, -1px -1px 0 #fff, 1px -1px 0 #fff, -1px 1px 0 #fff; }
  .pct.dem { color: var(--blue-text); top: -7px; }
  .pct.rep { color: var(--red-text); top: 20px; }

  .summary-band { position: absolute; left: 65px; top: 1094px; width: 848px; height: 75px; background: var(--navy-deep);
    color: var(--white); display: flex; align-items: center; justify-content: center; font-weight: 600; font-size: 27px; letter-spacing: -0.2px;
    text-shadow: 2px 2px 2px rgba(0,0,0,0.5); }
  .base-strip { position: absolute; left: 65px; top: 1169px; width: 848px; height: 31px; background: linear-gradient(#d2d4d7, #e4e5e7); }
</style>
</head>
<body>
<div class="canvas">
  <div class="survey-band">Based on a survey of 400 U.S. adults conducted March 20 - 24th, 2020</div>

  <header class="header">
    <div class="header-art" role="img" aria-label="Faint coronavirus particle illustrations scattered across the header"></div>
    <div class="title">
      <div class="title-lead">How likely it is that you will perform these</div>
      <div class="title-blue">behaviors to slow</div>
      <div class="title-row"><span class="title-script">the</span><span class="title-red">SPREAD OF</span></div>
      <div class="title-red second">CORONAVIRUS ?</div>
    </div>
  </header>

  <section class="chart-panel">
    <div class="map-area" role="img" aria-label="Dotted map of the United States in light grey"></div>

    <div class="legend">
      <span class="swatch dem"></span><span>DEMOCRATS</span>
      <span class="swatch rep"></span><span>REPUBLICANS</span>
    </div>

    <div class="rows">
      <div class="row" style="top:258px">
        <div class="row-label">ENGAGE IN SOCIAL DISTANCING</div>
        <div class="bar dem" style="width:359px"></div><div class="bar rep" style="width:363px"></div>
        <span class="pct dem" style="left:745px">81%</span><span class="pct rep" style="left:745px">82%</span>
      </div>
      <div class="row" style="top:313px">
        <div class="row-label">WORK FROM HOME</div>
        <div class="bar dem" style="width:288px"></div><div class="bar rep" style="width:266px"></div>
        <span class="pct dem" style="left:670px">65%</span><span class="pct rep" style="left:662px">60%</span>
      </div>
      <div class="row" style="top:368px">
        <div class="row-label">AVOID LARGE GATHERINGS</div>
        <div class="bar dem" style="width:372px"></div><div class="bar rep" style="width:377px"></div>
        <span class="pct dem" style="left:750px">84%</span><span class="pct rep" style="left:750px">85%</span>
      </div>
      <div class="row" style="top:423px">
        <div class="row-label">CANCEL SOCIAL ACTIVITIES</div>
        <div class="bar dem" style="width:354px"></div><div class="bar rep" style="width:363px"></div>
        <span class="pct dem" style="left:742px">80%</span><span class="pct rep" style="left:742px">82%</span>
      </div>
      <div class="row" style="top:478px">
        <div class="row-label">PUT DISTANCE BETWEEN YOUSELF<br>AND OTHER PEOPLE</div>
        <div class="bar dem" style="width:385px"></div><div class="bar rep" style="width:372px"></div>
        <span class="pct dem" style="left:755px">87%</span><span class="pct rep" style="left:755px">84%</span>
      </div>
      <div class="row" style="top:536px">
        <div class="row-label">WASH HANDS FOR<br>ATLEAST 20 SECONDS</div>
        <div class="bar dem" style="width:390px"></div><div class="bar rep" style="width:385px"></div>
        <span class="pct dem" style="left:760px">88%</span><span class="pct rep" style="left:760px">87%</span>
      </div>
      <div class="row" style="top:594px">
        <div class="row-label">USE HAND SANITIZER</div>
        <div class="bar dem" style="width:372px"></div><div class="bar rep" style="width:385px"></div>
        <span class="pct dem" style="left:755px">84%</span><span class="pct rep" style="left:755px">87%</span>
      </div>
      <div class="row" style="top:650px">
        <div class="row-label">AVOID TOUCHING YOUR EYES,<br>NOSE &amp; MOUTH</div>
        <div class="bar dem" style="width:363px"></div><div class="bar rep" style="width:354px"></div>
        <span class="pct dem" style="left:742px">82%</span><span class="pct rep" style="left:742px">80%</span>
      </div>
    </div>
  </section>

  <div class="summary-band">What does this table show? No big differences. Basically the same patterns</div>
  <div class="base-strip"></div>
</div>
</body>
</html>
```